Business Card Design needed for start up company Halvora

In need of a new business card designed for a start up company based in Sydney, Halvora is a new start up innovative Company, our mission it to make property accessible for everyday Australian and to become the leading Real Estate platform in Australia. We want it to be fresh and clean.

Industry/Entity Type

Financial

Contact Information for Business Card

Section for Name
Section for Title

HALVORA - The Strength of Pooling
Mobile:
Direct:

Font styles to use
Sans Serif

Colors
33a6d7
0692cd
0255a3
ffffff

Requirements
Must have
• Logo, all business card details

```html
<!DOCTYPE html>
<html lang="en">
<head>
<meta charset="utf-8">
<title>Halvora Business Card</title>
<link rel="stylesheet" href="https://fonts.googleapis.com/css2?family=Montserrat:wght@800&family=Open+Sans:wght@400;600;700&display=swap">
<style>
  :root {
    --backdrop: #929292;
    --navy: #203f77;
    --sky: #2a9fd8;
    --paper: #f2f2f2;
    --white: #ffffff;
    --ink: #2b2b2b;
  }
  html, body { margin: 0; padding: 0; overflow: hidden; }
  body {
    width: 1200px; height: 900px;
    background: var(--backdrop);
    position: relative;
    font-family: "Open Sans", Arial, sans-serif;
  }
  .card {
    position: absolute;
    top: 306px;
    height: 271px;
    border-radius: 10px;
    overflow: hidden;
  }
  .card-front {
    left: 149px; width: 439px;
    background: var(--paper);
  }
  .front-band {
    position: absolute; left: 357px; top: 0;
    width: 82px; height: 100%;
    background: var(--navy);
  }
  .front-badge {
    position: absolute; left: 293px; top: 72px;
    width: 100px; height: 100px;
    border-radius: 50%;
    background: var(--sky);
    border: 13px solid var(--paper);
  }
  .front-wordmark {
    position: absolute; left: 20px; top: 24px;
    margin: 0;
    font-family: "Montserrat", Arial, sans-serif;
    font-weight: 800;
    font-size: 51px;
    letter-spacing: -1px;
    color: var(--navy);
    line-height: 1;
  }
  .holder { position: absolute; left: 22px; top: 120px; }
  .holder-name {
    margin: 0;
    font-size: 15.5px; font-weight: 600;
    color: var(--navy); line-height: 1.2;
  }
  .holder-name .surname { color: var(--sky); }
  .holder-title {
    margin: 1px 0 0;
    font-size: 12px; color: var(--ink);
  }
  .contacts {
    position: absolute; left: 22px; top: 180px;
    margin: 0; padding: 0; list-style: none;
  }
  .contacts li {
    display: flex; align-items: center;
    height: 16px;
    font-size: 12px; color: var(--ink);
  }
  .contacts svg { width: 9px; height: 9px; margin-right: 6px; fill: var(--navy); }
  .card-back {
    left: 608px; width: 441px;
    background: var(--navy);
  }
  .back-lockup {
    position: absolute; left: 83px; top: 94px;
    display: flex; align-items: center;
  }
  .back-badge {
    width: 84px; height: 84px; border-radius: 50%;
    background: var(--sky);
    margin-right: 10px;
  }
  .back-wordmark {
    margin: 0;
    font-family: "Montserrat", Arial, sans-serif;
    font-weight: 800;
    font-size: 46px;
    letter-spacing: -1px;
    color: var(--white);
    line-height: 1;
  }
  .tagline {
    position: absolute; left: 0; right: 0; top: 192px;
    margin: 0; text-align: center;
    font-size: 12px; font-weight: 700;
    color: var(--white);
    letter-spacing: 0.2px;
  }
</style>
</head>
<body>
  <section class="card card-front" aria-label="Business card front">
    <div class="front-band"></div>
    <div class="front-badge"></div>
    <h1 class="front-wordmark">HALVORA</h1>
    <div class="holder">
      <p class="holder-name">DANIEL <span class="surname">REEVE</span></p>
      <p class="holder-title">Managing Director</p>
    </div>
    <ul class="contacts">
      <li><svg viewBox="0 0 10 10"><path d="M1 3c0-1 1-2 4-2s4 1 4 2v1H7V3H3v1H1zM2 5h6l1 4H1z"/></svg>044-987 654 321</li>
      <li><svg viewBox="0 0 10 10"><path d="M3 0h4a1 1 0 0 1 1 1v8a1 1 0 0 1-1 1H3a1 1 0 0 1-1-1V1a1 1 0 0 1 1-1zm0 1.5v6h4v-6zM5 8a.5.5 0 1 0 0 1 .5.5 0 0 0 0-1z"/></svg>044-987 654 322</li>
      <li><svg viewBox="0 0 10 10"><path d="M0 2h10v.6L5 6 0 2.6zM0 3.8 5 7l5-3.2V8H0z"/></svg>info@halvora.com</li>
      <li><svg viewBox="0 0 10 10"><circle cx="5" cy="5" r="4.5"/></svg>www.halvora.com</li>
    </ul>
  </section>

  <section class="card card-back" aria-label="Business card back">
    <div class="back-lockup">
      <div class="back-badge"></div>
      <h2 class="back-wordmark">HALVORA</h2>
    </div>
    <p class="tagline">THE STRENGTH OF POOLING</p>
  </section>
</body>
</html>
```